Business Card for a New Zealand IT Startup

I need a business card for VELTA Holdings. We are a young startup based in New Zealand working in internet marketing and web development. The design should have some element connected to New Zealand, such as wave, koru or silver fern, just don't use a kiwi bird.

```html
<!DOCTYPE html>
<html lang="en">
<head>
<meta charset="utf-8">
<title>VELTA Holdings – Business Card</title>
<link href="https://fonts.googleapis.com/css2?family=Source+Sans+3:wght@400;600;700&display=swap" rel="stylesheet">
<style>
  :root {
    --backdrop: #3a3b3d;
    --brand-blue: #0a68b4;
    --brand-orange: #e9561d;
    --paper: #ffffff;
    --ink-light: #ffffff;
  }
  * { margin: 0; padding: 0; box-sizing: border-box; }
  html, body { width: 1200px; height: 1000px; overflow: hidden; }
  body {
    background: var(--backdrop);
    font-family: "Source Sans 3", "Myriad Pro", sans-serif;
    position: relative;
  }
  .card {
    position: absolute;
    left: 215px;
    width: 770px;
    height: 440px;
    overflow: hidden;
    box-shadow: 0 10px 30px rgba(0,0,0,0.45);
  }
  .card-back { top: 40px; background: var(--brand-blue); }
  .card-front { top: 520px; background: var(--paper); }

  /* Back */
  .back-brand {
    position: absolute;
    top: 160px; left: 0; right: 0;
    display: flex; align-items: center; justify-content: center; gap: 18px;
    color: var(--ink-light);
  }
  .back-brand .brand-dot {
    width: 58px; height: 58px; border-radius: 50%; background: var(--ink-light);
  }
  .back-brand .brand-name {
    font-size: 54px; font-weight: 700; letter-spacing: 2px;
  }
  .back-website {
    position: absolute;
    top: 262px; left: 0; right: 0;
    text-align: center;
    color: var(--ink-light);
    font-size: 20px; letter-spacing: 4px;
  }

  /* Front */
  .front-art { position: absolute; inset: 0; width: 770px; height: 440px; }
  .front-brand {
    position: absolute;
    top: 44px; left: 300px;
    display: flex; align-items: center; gap: 14px;
    color: var(--brand-blue);
  }
  .front-brand .brand-name { font-size: 52px; font-weight: 700; letter-spacing: 1px; }
  .front-brand .brand-dot {
    width: 40px; height: 40px; border-radius: 50%; background: var(--brand-blue);
  }
  .holder {
    position: absolute;
    left: 42px; top: 222px;
    color: var(--ink-light);
    font-size: 19px; line-height: 1.2;
  }
  .holder .holder-name { font-weight: 700; font-size: 24px; letter-spacing: 0.5px; }
  .holder .holder-role { text-transform: uppercase; margin-bottom: 2px; }
  .contacts {
    position: absolute;
    right: 36px; top: 318px;
    list-style: none;
    color: var(--ink-light);
    font-size: 19px; line-height: 1.2;
    text-align: right;
  }
  .contacts li { display: flex; justify-content: flex-end; align-items: center; gap: 10px; }
  .contacts svg { width: 18px; height: 18px; fill: var(--ink-light); flex: none; }
</style>
</head>
<body>

<section class="card card-back" aria-label="Card back">
  <div class="back-brand">
    <span class="brand-dot"></span>
    <span class="brand-name">VELTA Holdings</span>
  </div>
  <p class="back-website">veltaholdings.com</p>
</section>

<section class="card card-front" aria-label="Card front">
  <svg class="front-art" viewBox="0 0 770 440" aria-hidden="true">
    <path d="M0,150 C200,130 380,180 500,262 C600,326 700,334 770,292 L770,440 L0,440 Z" fill="var(--brand-blue)"/>
    <path d="M0,136 C200,114 380,166 500,248 C600,312 700,320 770,278" fill="none" stroke="var(--brand-orange)" stroke-width="12"/>
    <path d="M0,162 C200,142 380,192 500,274 C600,338 700,346 770,304" fill="none" stroke="var(--paper)" stroke-width="2" opacity="0.8"/>
  </svg>

  <div class="front-brand">
    <span class="brand-name">VELTA Holdings</span>
    <span class="brand-dot"></span>
  </div>

  <div class="holder">
    <p class="holder-name">MARA TANE</p>
    <p class="holder-role">President</p>
    <p>42 Harbour View Road</p>
    <p>Wellington 6011, NZ</p>
  </div>

  <ul class="contacts">
    <li>021 448 3091
      <svg viewBox="0 0 24 24"><path d="M6.6 10.8a15 15 0 0 0 6.6 6.6l2.2-2.2a1 1 0 0 1 1-.25 11.4 11.4 0 0 0 3.6.57 1 1 0 0 1 1 1V20a1 1 0 0 1-1 1A17 17 0 0 1 3 4a1 1 0 0 1 1-1h3.5a1 1 0 0 1 1 1c0 1.25.2 2.45.57 3.57a1 1 0 0 1-.25 1z"/></svg>
    </li>
    <li>027 615 2840
      <svg viewBox="0 0 24 24"><path d="M7 2h10a2 2 0 0 1 2 2v16a2 2 0 0 1-2 2H7a2 2 0 0 1-2-2V4a2 2 0 0 1 2-2zm0 3v13h10V5zm5 14.2a1 1 0 1 0 0 .01z"/></svg>
    </li>
    <li>04 902 7713
      <svg viewBox="0 0 24 24"><path d="M7 3h9l2 2v4H7zM4 10h16a2 2 0 0 1 2 2v7H2v-7a2 2 0 0 1 2-2zm3 7h10v4H7z"/></svg>
    </li>
    <li>mara@veltaholdings.com
      <svg viewBox="0 0 24 24"><path d="M3 5h18a1 1 0 0 1 1 1v12a1 1 0 0 1-1 1H3a1 1 0 0 1-1-1V6a1 1 0 0 1 1-1zm0 2v.4l9 5.6 9-5.6V7z"/></svg>
    </li>
  </ul>
</section>

</body>
</html>
```